A specialised Sport management needs a corporate brochure design

We are a specialized company in the management and consultancy of sports events. and need to have a company brochure
We provide the following services;
Event management
Venues management
Production
Ticketing
Consulting
Hospitality
Activity management
Event timing
Branding of event
Event supplies
We need a corporate profile design for our company to showcase the major events that we have covered , with images, information, statistics, surveys, products and services used. We want to highlight our professionalism and execution of the events, experience of the participants, spectators . How we have grown in the past few years and reached the international standards.
Objectives of the work:
To get sponsors and partners for future business and to present Tri-Crest
as not just a sports management company but also a professional sports
events management company.
You can check our website
www.tri-crest.example
Target Market(s)
Sponsors and corporate partners
Industry/Entity Type
Events
Requirements
Must have
- Must Have:
- - Very professional look
- -Some event images,Event information, statistics, surveys, products and services used. We want to highlight our professionalism and execution of the events (Attached)
Nice to have
- Similar momentom of the below design
- http://www.lumavent.example/wp-content/themes/lumavent/pdf/CP-2014-15-V10-Web.pdf

```html
<!DOCTYPE html>
<html lang="en">
<head>
<meta charset="utf-8">
<title>Tri-Crest Brochure – Target Segment</title>
<link href="https://fonts.googleapis.com/css2?family=Didact+Gothic&family=Questrial&display=swap" rel="stylesheet">
<style>
  :root {
    --page-bg: #ece8e2;
    --charcoal: #262626;
    --white: #ffffff;
    --title-ink: #e8f6f8;
    --accent-red: #e5432a;
    --accent-orange: #f07a1a;
    --accent-amber: #f6a53a;
    --ink: #2b2b2b;
    --mist-1: #c9ccc8;
    --mist-2: #8e948f;
    --crowd-1: #6d6a66;
    --crowd-2: #b5aaa0;
    --sky-1: #7fb7dd;
    --sky-2: #c6a47c;
    --track-1: #c8351e;
    --track-2: #7a2012;
  }
  * { box-sizing: border-box; margin: 0; padding: 0; }
  html, body { width: 1200px; height: 509px; overflow: hidden; background: var(--page-bg); }
  .canvas { position: relative; width: 1200px; height: 509px; }
  .spread {
    position: absolute; left: 20px; top: 20px; width: 1160px; height: 470px;
    box-shadow: 0 6px 18px rgba(0,0,0,.25);
    overflow: hidden;
  }
  .spread-art { position: absolute; inset: 0; }

  .segment {
    position: absolute; left: 247px; top: 160px; width: 332px;
    font-family: "Didact Gothic", "Questrial", sans-serif; color: var(--white);
  }
  .segment-title {
    font-family: "Questrial", sans-serif; font-weight: 400;
    font-size: 19px; letter-spacing: 1px; color: var(--title-ink); line-height: 24px;
  }
  .segment-group { margin-top: 6px; }
  .segment-group:first-of-type { margin-top: 22px; }
  .segment-heading {
    font-family: "Questrial", sans-serif; font-weight: 400;
    font-size: 15px; color: var(--accent-red); line-height: 17px;
  }
  .segment-body { font-size: 11.3px; line-height: 14.5px; letter-spacing: .15px; }
  .segment-body .line { display: block; white-space: nowrap; text-align: justify; text-align-last: justify; }
  .segment-body .line.last { text-align-last: left; }

  .stat {
    position: absolute; width: 170px; text-align: center;
    font-family: "Didact Gothic", "Questrial", sans-serif; color: var(--ink);
  }
  .stat-label { font-size: 15px; line-height: 17px; }
  .stat-figure { font-size: 21px; color: var(--accent-red); line-height: 22px; }
  .stat-note { font-size: 10.5px; line-height: 13.5px; margin-top: 3px; }
  .stat-percent { font-size: 19px; color: var(--accent-red); margin-top: 4px; }
  .stat-one { left: 612px; top: 88px; }
  .stat-two { left: 787px; top: 104px; }
  .stat-three { left: 717px; top: 268px; }
  .stat-three .stat-figure { margin-top: 8px; }
  .stat-three .stat-note { margin-top: 6px; }
</style>
</head>
<body>
<div class="canvas">
  <div class="spread">
    <svg class="spread-art" width="1160" height="470" viewBox="0 0 1160 470">
      <defs>
        <linearGradient id="mist" x1="0" y1="0" x2="0" y2="1">
          <stop offset="0" stop-color="var(--mist-1)"/><stop offset="1" stop-color="var(--mist-2)"/>
        </linearGradient>
        <linearGradient id="crowd" x1="0" y1="0" x2="1" y2="1">
          <stop offset="0" stop-color="var(--crowd-2)"/><stop offset="1" stop-color="var(--crowd-1)"/>
        </linearGradient>
        <linearGradient id="sky" x1="0" y1="0" x2="1" y2="1">
          <stop offset="0" stop-color="var(--sky-1)"/><stop offset="1" stop-color="var(--sky-2)"/>
        </linearGradient>
        <linearGradient id="track" x1="0" y1="0" x2="0" y2="1">
          <stop offset="0" stop-color="var(--track-1)"/><stop offset="1" stop-color="var(--track-2)"/>
        </linearGradient>
        <radialGradient id="disc" cx="0.5" cy="0.45" r="0.55">
          <stop offset="0.6" stop-color="#ffffff"/><stop offset="1" stop-color="#dcdcdc"/>
        </radialGradient>
        <linearGradient id="brush" x1="0" y1="0" x2="1" y2="1">
          <stop offset="0" stop-color="var(--accent-amber)"/><stop offset="1" stop-color="var(--accent-orange)"/>
        </linearGradient>
      </defs>

      <rect class="photo-crowd" width="1160" height="470" fill="url(#crowd)" role="img" aria-label="Photo: event host speaking into a microphone in front of a crowd"/>
      <polygon class="photo-mountains" points="0,0 620,0 620,75 230,130 0,130" fill="url(#mist)" role="img" aria-label="Photo: misty limestone mountains at dawn"/>
      <polygon class="photo-runner" points="830,0 1160,0 1160,230 1040,270" fill="url(#sky)" role="img" aria-label="Photo: trail runner climbing past desert rocks"/>
      <polygon class="photo-track" points="330,470 580,380 1040,270 1160,230 1160,470" fill="url(#track)" role="img" aria-label="Photo: motion-blurred athlete on a red running track"/>

      <polygon class="panel-dark" points="230,130 580,80 580,380 330,470 35,470" fill="var(--charcoal)"/>
      <polygon class="panel-white" points="580,80 600,0 830,0 1040,270 580,380" fill="var(--white)"/>

      <g class="stat-rings">
        <circle cx="697" cy="152" r="82" fill="none" stroke="url(#brush)" stroke-width="16" opacity=".9"/>
        <circle cx="697" cy="152" r="72" fill="url(#disc)"/>
        <circle cx="872" cy="152" r="82" fill="none" stroke="url(#brush)" stroke-width="16" opacity=".9"/>
        <circle cx="872" cy="152" r="72" fill="url(#disc)"/>
        <circle cx="782" cy="318" r="82" fill="none" stroke="url(#brush)" stroke-width="16" opacity=".9"/>
        <circle cx="782" cy="318" r="72" fill="url(#disc)"/>
      </g>
    </svg>

    <section class="segment">
      <h2 class="segment-title">TARGET SEGMENT</h2>
      <div class="segment-group">
        <h3 class="segment-heading">Mainstream Public</h3>
        <p class="segment-body">
          <span class="line">This is a huge audience reached predominantly through</span>
          <span class="line">the mainstream print and digital coverage. They are</span>
          <span class="line">captivated and inspired by the incredible feats of sport</span>
          <span class="line">events and determination displayed by the athletes.</span>
          <span class="line last">Estimated number of mainstream audience is 50,000</span>
        </p>
      </div>
      <div class="segment-group">
        <h3 class="segment-heading">Engaged:</h3>
        <p class="segment-body">
          <span class="line">This segment encompasses all those who are engaged</span>
          <span class="line last">directly with us, but not necessarily a current athlete.</span>
        </p>
      </div>
      <div class="segment-group">
        <h3 class="segment-heading">Athletes</h3>
        <p class="segment-body">
          <span class="line">Majority of athletes are ranging between 20 - 45 years</span>
          <span class="line last">old, %70 Male and %30 Female , with high disposable</span>
          <span class="line">incomes. They are fit, motivated and looking to challenge</span>
          <span class="line last">themselves.</span>
        </p>
      </div>
    </section>

    <div class="stat stat-one">
      <div class="stat-label">Number of<br>Participates in 2014</div>
      <div class="stat-figure">10,000</div>
      <div class="stat-note">Said they would rate our<br>events as "Excellent" in our<br>survey (average)</div>
      <div class="stat-percent">86%</div>
    </div>
    <div class="stat stat-two">
      <div class="stat-label">Number of<br>Sports</div>
      <div class="stat-figure">13</div>
      <div class="stat-note">Said they would participate<br>again (average)</div>
      <div class="stat-percent">84%</div>
    </div>
    <div class="stat stat-three">
      <div class="stat-label">Visitors</div>
      <div class="stat-figure">+30,000</div>
      <div class="stat-note">Said they recognized our<br>sponsors (average)</div>
      <div class="stat-percent">80%</div>
    </div>
  </div>
</div>
</body>
</html>
```